Corporate Business Card

Very professional, Modern, Not to busy, include phone address email, website
(360) 617-4930, 18761 52nd Avenue S, Dunmore, OR 98047, martin@plumlinegroup.com, varkoworks.com

Target Market(s)

Manufacturing

Industry/Entity Type

Aero, machining, manufacturing, Off road racing

Contact Information for Business Card

Phone, address email, website

```html
<!DOCTYPE html>
<html lang="en">
<head>
<meta charset="utf-8">
<title>Varko Works – Business Card</title>
<link href="https://fonts.googleapis.com/css2?family=Lato:wght@400;900&display=swap" rel="stylesheet">
<style>
  :root {
    --navy: #1b3570;
    --red: #d0222e;
    --paper: #ffffff;
    --paper-shade: #eeeeee;
    --ink: #333a45;
    --backdrop: #e4e5e7;
  }
  * { margin: 0; padding: 0; box-sizing: border-box; }
  html, body { width: 1200px; height: 900px; overflow: hidden; }
  body {
    background: var(--backdrop);
    font-family: 'Lato', sans-serif;
    position: relative;
  }
  .card {
    position: absolute;
    left: 250px;
    width: 700px;
    height: 400px;
    background: linear-gradient(120deg, var(--paper) 0%, var(--paper) 55%, var(--paper-shade) 100%);
    box-shadow: 0 6px 18px rgba(0,0,0,0.18);
    overflow: hidden;
  }
  .card--front { top: 30px; }
  .card--back { top: 470px; }

  .card__bands {
    position: absolute;
    left: 0; right: 0; bottom: 0;
  }
  .card__band { height: 11px; }
  .card__band--navy { background: var(--navy); }
  .card__band--red { background: var(--red); }

  .brand-name {
    position: absolute;
    left: 0; right: 0;
    text-align: center;
    font-weight: 900;
    font-size: 60px;
    line-height: 1;
    color: var(--navy);
    letter-spacing: 1px;
  }
  .card--front .brand-name { top: 160px; }
  .card--back .brand-name { top: 70px; }

  .contact {
    position: absolute;
    list-style: none;
    font-size: 17px;
    color: var(--ink);
  }
  .contact li {
    display: flex;
    align-items: center;
    gap: 8px;
    margin-bottom: 10px;
  }
  .contact--online { right: 40px; top: 200px; }
  .contact--online li { justify-content: flex-end; }
  .contact--office { left: 40px; bottom: 50px; }
  .icon { width: 16px; height: 16px; flex: none; }
  .icon--navy { fill: var(--navy); }
  .icon--red { fill: var(--red); }
</style>
</head>
<body>

<section class="card card--front" aria-label="Card front">
  <p class="brand-name">Varko Works</p>
  <div class="card__bands">
    <div class="card__band card__band--navy"></div>
    <div class="card__band card__band--red"></div>
  </div>
</section>

<section class="card card--back" aria-label="Card back">
  <p class="brand-name">Varko Works</p>

  <ul class="contact contact--online">
    <li>www.varkoworks.com
      <svg class="icon icon--navy" viewBox="0 0 16 16" aria-hidden="true"><path d="M8 1a7 7 0 1 0 0 14A7 7 0 0 0 8 1zm0 1.5c.8 0 1.7 1.4 2 3.5H6c.3-2.1 1.2-3.5 2-3.5zM2.6 7h2.3c0 .7 0 1.3.1 2H2.6a5.6 5.6 0 0 1 0-2zm3.3 0h4.2c0 .7 0 1.4-.1 2H6c-.1-.6-.1-1.3-.1-2zm5.2 0h2.3a5.6 5.6 0 0 1 0 2H11c.1-.7.1-1.3.1-2zM6 10h4c-.3 2.1-1.2 3.5-2 3.5S6.3 12.1 6 10z"/></svg>
    </li>
    <li>martin@plumlinegroup.com
      <svg class="icon icon--red" viewBox="0 0 16 16" aria-hidden="true"><path d="M1 4h14v9H1z"/><path d="M1.5 4.5 8 9l6.5-4.5" stroke="#fff" stroke-width="1.2" fill="none"/></svg>
    </li>
  </ul>

  <ul class="contact contact--office">
    <li>
      <svg class="icon icon--navy" viewBox="0 0 16 16" aria-hidden="true"><path d="M3.6 1.5 6 4 4.8 5.6a9 9 0 0 0 5.6 5.6L12 10l2.5 2.4-1.6 2.1C7.5 14.5 1.5 8.5 1.5 3.1z"/></svg>
      (360) 617-4930
    </li>
    <li>
      <svg class="icon icon--red" viewBox="0 0 16 16" aria-hidden="true"><path d="M8 1a5 5 0 0 0-5 5c0 3.6 5 9 5 9s5-5.4 5-9a5 5 0 0 0-5-5zm0 7a2 2 0 1 1 0-4 2 2 0 0 1 0 4z"/></svg>
      18761 52nd Avenue S, Dunmore, OR 98047
    </li>
  </ul>

  <div class="card__bands">
    <div class="card__band card__band--navy"></div>
    <div class="card__band card__band--red"></div>
  </div>
</section>

</body>
</html>
```